Luxury Wine Label for New Startup Winery

We need a wine label for our new winery startup. We have worked with a local designer but do not feel the resulting label / logo have the elevation required to present our brand as a luxury wine. Our winery is called "Quailbrook Vineyards" and we are focused on extremely high quality hand crafted artisan and estate wines from the Pacific Northwest.
We would like to see designs that utilize a tree line, or other imagery that represents the "Quailbrook" part of our company name. Another interesting feature could be wood grain.
A logo will be required based on your design so please design with this in mind:
This logo should be consistent with the wine bottle label design, and should be representative of our high end exclusive wine while giving a sense of place (Oregon/ Pacific Northwest.)
I will supply an image of the design we received from our local designer, PLEASE NOTE: in general we do like wood grain and tree line concepts but feel the execution was poorly done.
ATTN: Logo design should be suitable for use on: Bottles (Red wine/rose/white wine), Bussiness cards, vehicle signage, business signage, etc
P.S.:
If you have a design that is not outside the box we are still interested in seeing it.
Label is for a burgundy style bottle with a label height of 3.5 - 4" and a width of 3.5-4"
any label <= 4"x4" and >=3.5"x3.5" will be acceptable:
HOWEVER Width should be greater than or equal to height due to the bottle format
Target Market(s)
Wine enthusiasts with adequate discretionary budgets to afford $100 bottles of wine.
Industry/Entity Type
Wine / Winery
Requirements
Must have
- A sense of luxury, a feel of exclusivity, and a theme consistent with our product and brand name
Nice to have
- Tree line, wood grain or other wood themes. Serif fonts
Should not have
- anything cheesy, off topic, hard to read script fonts or anything that makes the label hard to read from a few feet away or too busy

```html
<!DOCTYPE html>
<html lang="en">
<head>
<meta charset="utf-8">
<title>Quailbrook Vineyards – Syrah Label</title>
<link href="https://fonts.googleapis.com/css2?family=Libre+Caslon+Text:wght@400;700&family=Crimson+Pro:wght@500;600&display=swap" rel="stylesheet">
<style>
  :root {
    --night: #17191b;
    --night-soft: #25282b;
    --wood-dark: #5a2a08;
    --wood-mid: #8a4410;
    --wood-light: #a5581c;
    --gold: #d9a21c;
    --gold-light: #f3d566;
    --gold-deep: #9c6f0c;
    --cream: #f4efe4;
    --etch-light: #e6e6e2;
    --etch-dark: #4a4a48;
    --tree-shade: rgba(70, 38, 14, 0.55);
  }
  * { margin: 0; padding: 0; box-sizing: border-box; }
  html, body { width: 1050px; height: 1200px; overflow: hidden; background: var(--night); }
  .label {
    position: relative;
    width: 1050px;
    height: 1200px;
    overflow: hidden;
    font-family: "Libre Caslon Text", Georgia, serif;
  }
  .label__night {
    position: absolute; left: 0; top: 0; width: 1050px; height: 532px;
    background: radial-gradient(ellipse at 50% 40%, var(--night-soft), var(--night) 75%);
  }
  .label__wood {
    position: absolute; left: 0; top: 532px; width: 1050px; height: 668px;
    background: linear-gradient(90deg, var(--wood-dark), var(--wood-mid) 20%, var(--wood-light) 45%, var(--wood-mid) 70%, var(--wood-dark));
  }
  .label__treeline {
    position: absolute; left: 240px; top: 490px; width: 570px; height: 260px;
    background: linear-gradient(180deg, rgba(70,38,14,0) 0%, var(--tree-shade) 45%, var(--tree-shade) 100%);
  }
  .label__art { position: absolute; left: 0; top: 0; }
  .brand-name {
    position: absolute; left: 0; width: 1050px; top: 338px;
    text-align: center; color: var(--cream);
    font-size: 88px; font-weight: 400; letter-spacing: 9px; line-height: 1;
  }
  .brand-sub {
    position: absolute; left: 0; width: 1050px; top: 455px;
    text-align: center; color: var(--cream);
    font-size: 38px; letter-spacing: 6px; line-height: 1;
  }
  .appellation {
    position: absolute; left: 0; width: 1050px; top: 548px;
    text-align: center; color: var(--cream);
    font-family: "Crimson Pro", Georgia, serif; font-weight: 600;
    font-size: 52px; line-height: 1;
    text-shadow: 3px 3px 2px rgba(0,0,0,0.75);
  }
  .varietal {
    position: absolute; left: 0; width: 1050px; top: 650px;
    text-align: center; color: #ffffff;
    font-family: "Crimson Pro", Georgia, serif; font-weight: 600;
    font-size: 86px; letter-spacing: 2px; line-height: 1;
    text-shadow: 4px 4px 3px rgba(0,0,0,0.8);
  }
  .vintage-line {
    position: absolute; left: 0; width: 1050px; top: 1072px;
    text-align: center; color: var(--cream);
    font-size: 42px; letter-spacing: 6px; line-height: 1;
  }
</style>
</head>
<body>
<main class="label">
  <div class="label__night"></div>
  <div class="label__wood" role="img" aria-label="Warm brown wood grain background"></div>
  <div class="label__treeline" role="img" aria-label="Faint silhouette of a line of evergreen trees"></div>

  <svg class="label__art" width="1050" height="1200" viewBox="0 0 1050 1200" aria-hidden="false">
    <defs>
      <linearGradient id="gold" x1="0" y1="0" x2="1" y2="1">
        <stop offset="0" stop-color="var(--gold-light)"/>
        <stop offset="0.5" stop-color="var(--gold)"/>
        <stop offset="1" stop-color="var(--gold-deep)"/>
      </linearGradient>
      <linearGradient id="etch" x1="0" y1="0" x2="0" y2="1">
        <stop offset="0" stop-color="var(--etch-light)"/>
        <stop offset="1" stop-color="var(--etch-dark)"/>
      </linearGradient>
      <linearGradient id="etch-low" x1="0" y1="0" x2="0" y2="1">
        <stop offset="0" stop-color="#8a8a86"/>
        <stop offset="1" stop-color="#2e2e2c"/>
      </linearGradient>
    </defs>

    <!-- frames -->
    <polyline class="frame frame--top" points="64,532 64,24 988,24 988,532" fill="none" stroke="url(#gold)" stroke-width="5"/>
    <polyline class="frame frame--bottom" points="64,660 64,1172 988,1172 988,660" fill="none" stroke="url(#gold)" stroke-width="5"/>

    <!-- upper vignette -->
    <path d="M240 340 A285 285 0 0 1 810 340" fill="none" stroke="url(#gold)" stroke-width="10"/>
    <path d="M256 340 A269 269 0 0 1 794 340" fill="none" stroke="url(#gold)" stroke-width="4"/>
    <path role="img" aria-label="Etched vineyard rows stretching to a farmhouse under a clouded sky" d="M265 338 A260 260 0 0 1 785 338 Z" fill="url(#etch)"/>

    <!-- lower vignette -->
    <path d="M240 750 A285 285 0 0 0 810 750" fill="none" stroke="url(#gold)" stroke-width="10"/>
    <path d="M256 750 A269 269 0 0 0 794 750" fill="none" stroke="url(#gold)" stroke-width="4"/>
    <path role="img" aria-label="Close-up etched vineyard rows" d="M265 752 A260 240 0 0 0 785 752 Z" fill="url(#etch-low)"/>

    <!-- rules beside subtitle -->
    <line x1="205" y1="482" x2="356" y2="482" stroke="var(--cream)" stroke-width="3"/>
    <line x1="693" y1="482" x2="845" y2="482" stroke="var(--cream)" stroke-width="3"/>
  </svg>

  <h1 class="brand-name">QUAILBROOK</h1>
  <p class="brand-sub">VINEYARDS</p>
  <p class="appellation">-WILLAMETTE VALLEY-</p>
  <h2 class="varietal">SYRAH</h2>
  <p class="vintage-line">''ESTATE | 2023 | GROWN"</p>
</main>
</body>
</html>
```